Brochure for a website accessibility report

This brochure is related to a report that www.qelvantrix.org sell. The report shows the results of an automated audit of a websites accessibility. It shows details of issues found with screen shots, examples of code and provides remediation advice.

The brochure will be a pdf 8.5 inches by 11 inches. It can be anywhere from 6 to 10 pages.

The FlintVue™ name itself should be “Bree Serif” font. The fonts, styles, colors and sizes are up to you.

The images used and logo of the Office of Digital Reachworks and K7P logo are upload

We highlighted in blue page extracts from the report we sell. Do not use the blue highlight, it is merely there to show you where the specific examples of the report we sell are vs the other content in the report. The areas in blue which show the content from the actual report should be shown as an extract of the actual page of the report. You have flexibility to change the layout and the way the content look.

The red square callouts over the blue content are callouts that describe the specific page extracts. We used it as a red callout only so that you would be able to see it. You should change the specific location, look and feel of the callout to be appropriate

Target Market(s)

Marketing and Technical people

Industry/Entity Type

Information Technology

Font styles to use
Sans Serif

Colors

Designer to choose colors to be used in the design.

Requirements
Should not have
• wheelchairs, images of blind people

```html
<!DOCTYPE html>
<html lang="en">
<head>
<meta charset="utf-8">
<title>FlintVue™ Report – Perceivable</title>
<link rel="stylesheet" href="https://fonts.googleapis.com/css2?family=Arimo:ital,wght@0,400;0,700;1,400&family=Bree+Serif&family=Courier+Prime&display=swap">
<style>
  :root{
    --green:#27b36a;
    --green-text:#3aa83a;
    --panel:#d9ebdf;
    --mark:#e3efe6;
    --ink:#111;
    --red:#d0202a;
    --code:#6f6f6f;
    --link:#1a3fa8;
  }
  *{margin:0;padding:0;box-sizing:border-box}
  html,body{width:1200px;height:927px;overflow:hidden;background:#fff}
  body{position:relative;font-family:"Arimo",Arial,sans-serif;color:var(--ink)}
  .brand{position:absolute;left:1087px;top:7px;display:flex;align-items:center;gap:5px}
  .brand-square{width:18px;height:60px;background:var(--green)}
  .brand-name{font-weight:700;font-size:11.5px;line-height:13px;color:#111;text-transform:uppercase}
  .side-mark{position:absolute;left:1132px;top:214px;width:70px;height:470px;overflow:hidden}
  .side-mark span{position:absolute;left:70px;top:0;transform-origin:0 0;transform:rotate(90deg);font-family:"Bree Serif",serif;font-size:86px;line-height:70px;color:var(--mark);white-space:nowrap}

  .block{position:absolute;left:109px;width:982px}
  .body-text{font-size:16.4px;line-height:20px;text-align:justify}
  .intro{top:105px;font-size:17.4px;line-height:22px}
  .principle{top:150px;color:var(--green-text);font-size:21.5px;font-weight:700;text-align:center;line-height:24px}
  .principle-text{top:174px}
  .guideline{top:261px;font-size:17.5px;font-weight:700;text-align:center;line-height:22px}
  .guideline-text{top:281px;line-height:21px}
  .issue{top:323px;color:var(--green-text);font-size:17.5px;font-weight:700;text-align:center;line-height:22px}
  .rule{top:345px;line-height:22px}
  .lead{font-size:17.5px;font-weight:700}
  .example{top:396px;text-align:center;font-size:17px;line-height:20px}
  .example a{color:var(--link)}

  .panel{position:absolute;left:109px;top:418px;width:982px;height:396px;background:var(--panel)}
  .divider{position:absolute;left:465px;top:0;width:4px;height:396px;background:var(--green)}
  .shot{position:absolute;left:15px;top:6px;width:436px;height:350px;background:#fff;overflow:hidden}
  .callout{position:absolute;color:var(--red);font-style:italic;font-size:13.8px;line-height:16px}
  .callout.left{left:20px;top:360px;width:440px}
  .callout.right{left:508px;top:79px;width:450px}
  .specs{position:absolute;left:508px;top:135px;width:470px;font-size:17px;line-height:21px}
  .specs h5{font-size:17.5px;font-weight:700;line-height:22px}
  .mono{font-family:"Courier Prime","Courier New",monospace;color:var(--code);font-size:16.4px;white-space:nowrap}
  .code{margin-top:16px}
  .code .mono{display:block;line-height:20px}
  .page-no{position:absolute;left:1091px;top:818px;width:109px;height:109px;background:var(--green);color:#fff;font-size:17px;display:flex;align-items:center;justify-content:center}
</style>
</head>
<body>
  <div class="brand">
    <div class="brand-square"></div>
    <div class="brand-name">Office of<br>Digital<br>Reachworks</div>
  </div>

  <div class="side-mark" aria-hidden="true"><span>FlintVue™</span></div>

  <p class="block intro">The report then provides full detail about the specific infractions organized by each of the four principles and explains exactly what the problems are. Example:</p>
  <h2 class="block principle">Principle 1 - Perceivable</h2>
  <p class="block body-text principle-text">Information and user interface components must be presentable to users in ways they can perceive. This means that users must be able to perceive the information being presented (it can’t be invisible to all of their senses). Provide text alternatives for non-text content. Provide captions and other alternatives for multimedia. Create content that can be presented in different ways, including by assistive technologies, without losing meaning. Make it easier for users to see and hear content.</p>
  <h3 class="block guideline">Guideline 1.1 Text Alternatives</h3>
  <p class="block body-text guideline-text">Provide text alternatives for any non-text content so that it can be changed into other forms people need, such as large print, braille, speech, symbols or simpler language.</p>
  <h4 class="block issue">Issue: Field Element Labels</h4>
  <p class="block body-text rule"><span class="lead">Each form control should be explicitly associated with its label.</span> Form fields must be associated with their labels. Issue is relevant to checkpoints: 1.1.1 (A), 1.3.1 (A), 4.1.2 (A), 3.3.2 (A)</p>
  <p class="block example">Example: <a href="#">http://www.norvali.org/en/events/childrenday/</a></p>

  <section class="panel">
    <div class="shot">
      <svg width="436" height="350" viewBox="0 0 436 350">
        <defs><linearGradient id="photo" x1="0" y1="0" x2="1" y2="1"><stop offset="0" stop-color="#8a7560"/><stop offset="1" stop-color="#4a3e33"/></linearGradient></defs>
        <rect x="0" y="11" width="430" height="2" fill="#1e9bd7"/>
        <rect x="24" y="4" width="60" height="3" fill="#bbb"/>
        <rect x="320" y="4" width="100" height="3" fill="#bbb"/>
        <circle cx="33" cy="40" r="15" fill="#cfe3f3"/>
        <rect x="55" y="33" width="95" height="5" fill="#444"/>
        <rect x="55" y="42" width="55" height="5" fill="#444"/>
        <rect x="316" y="33" width="56" height="14" fill="#fff" stroke="#e0602a" stroke-width="1.5"/>
        <rect x="320" y="38" width="14" height="3" fill="#bbb"/>
        <circle cx="336" cy="24" r="4" fill="#d0202a"/>
        <path d="M333 26 L336 32 L339 26 Z" fill="#d0202a"/>
        <rect x="400" y="33" width="12" height="12" fill="#1e9bd7"/>
        <rect x="16" y="67" width="67" height="11" fill="#eee"/>
        <rect x="83" y="67" width="330" height="11" fill="#2f3a44"/>
        <rect x="16" y="84" width="397" height="168" fill="url(#photo)" role="img" aria-label="Photo of children holding up hand-drawn signs calling for peace"/>
        <rect x="30" y="256" width="370" height="3" fill="#c7c7c7"/>
        <rect x="50" y="262" width="320" height="3" fill="#c7c7c7"/>
        <g fill="#c9c9c9">
          <rect x="20" y="279" width="380" height="3"/><rect x="20" y="285" width="100" height="3"/>
          <rect x="20" y="296" width="385" height="3"/><rect x="20" y="302" width="150" height="3"/>
          <rect x="20" y="313" width="360" height="3"/>
          <rect x="20" y="324" width="385" height="3"/><rect x="20" y="330" width="330" height="3"/>
          <rect x="20" y="341" width="385" height="3"/>
        </g>
        <rect x="428" y="0" width="6" height="350" fill="#f1f1f1"/>
        <rect x="429" y="6" width="4" height="220" fill="#c4c4c4"/>
      </svg>
    </div>
    <div class="divider"></div>
    <p class="callout left">Actual screen shots of your website pages are shown so you can see<br>exactly where the “Issues Discovered” are present</p>
    <p class="callout right">The specifics of the failure and a code snippets pinpoint within the code where the issue resided.</p>
    <div class="specs">
      <h5>Specifics:</h5>
      <p>Each form field should be explicitly associated with its label.</p>
      <p>Found <span class="mono">No explicit Label provided</span></p>
      <p style="padding-left:54px"><span class="mono">&lt;INPUT&gt; Tag type=text id=’search-sm’ .</span></p>
      <div class="code">
        <h5>Code snippet:</h5>
        <span class="mono">&lt;input class=”search-control form-control”</span>
        <span class="mono">type=”text” name=”q” id=”search-sm”</span>
        <span class="mono">onfocus=”this.value=’’;” value=”Search”&gt;</span>
      </div>
    </div>
  </section>

  <div class="page-no">5</div>
</body>
</html>
```